Young, dynamic furniture company needs a new business card design

We require a new business card design for our modern furniture company which supplies furniture and appliances to the property and development market.
Oakridge Interiors has become one of the leading furniture & appliance suppliers to the property market withing London. With over 10 years experience, we have increased our business to supply not only private landlords and managing agents, but also property developers, housing associations and local councils.
We offer not only a complete range of furniture which includes beds, wardrobes, dining sets and sofas, but also a high quality, full delivery and assembly service to help you with all our furnishing needs.

Target Market(s)

Private landlords, estate agents, letting agents, property management companies

Industry/Entity Type

Business

Contact Information for Business Card

Name,
Title,
Address,
Mobile,
Telephone,
Fax, Website, email address

Font styles to use
Sans Serif

Colors
3176b5
0555a3
85abd2
cfdeed

Requirements
Must have
• All the above information for each of our staff, along with our logo

```html
<!DOCTYPE html>
<html lang="en">
<head>
<meta charset="utf-8">
<title>Oakridge Interiors – Business Card</title>
<link rel="stylesheet" href="https://fonts.googleapis.com/css2?family=Open+Sans:wght@300;400;600;700&display=swap">
<style>
  :root {
    --page-bg: #e8e9ee;
    --card-white: #f4f5f7;
    --brand-blue: #2a4fa6;
    --brand-blue-deep: #1c2f8a;
    --brand-blue-light: #3176b5;
    --accent-sky: #85abd2;
    --curve-dark: #1f2026;
    --ink: #2a2b30;
    --ink-soft: #55575f;
    --white: #ffffff;
  }
  * { box-sizing: border-box; margin: 0; padding: 0; }
  html, body {
    width: 1200px; height: 780px; overflow: hidden;
    background: var(--page-bg);
    font-family: "Open Sans", Arial, sans-serif;
  }
  .canvas { position: relative; width: 1200px; height: 780px; }

  .card {
    position: absolute; top: 235px;
    width: 540px; height: 310px;
    border-radius: 4px; overflow: hidden;
    box-shadow: 0 14px 30px rgba(20, 25, 50, .22);
  }
  .card--front { left: 40px; background: var(--card-white); }
  .card--back {
    left: 620px;
    background: radial-gradient(ellipse at 45% 40%, #3149b0 0%, var(--brand-blue-deep) 80%);
  }

  .front-shape { position: absolute; inset: 0; }

  .contact {
    position: absolute; left: 290px; top: 22px;
    color: var(--white);
  }
  .contact__name { font-weight: 700; font-size: 17px; letter-spacing: .3px; line-height: 20px; }
  .contact__title { font-size: 11px; line-height: 14px; margin-bottom: 6px; }
  .contact__address { font-size: 11.5px; line-height: 15px; }
  .contact__list { list-style: none; margin-top: 2px; }
  .contact__row { display: flex; align-items: center; font-size: 11.5px; line-height: 16px; }
  .contact__icon {
    width: 13px; height: 13px; margin-right: 6px;
    background: var(--white); border-radius: 1px;
    display: flex; align-items: center; justify-content: center;
  }
  .contact__icon svg { width: 9px; height: 9px; }

  .brand { position: absolute; display: flex; align-items: center; }
  .brand__square { width: 34px; height: 34px; margin-right: 12px; }
  .brand__name { font-weight: 400; font-size: 19px; letter-spacing: .5px; line-height: 22px; text-transform: uppercase; }
  .brand__tagline { font-weight: 300; font-size: 9.5px; letter-spacing: .6px; text-transform: uppercase; }

  .brand--front { left: 42px; top: 212px; }
  .brand--front .brand__square { background: var(--brand-blue-light); }
  .brand--front .brand__name { color: var(--ink); }
  .brand--front .brand__tagline { color: var(--ink-soft); }

  .brand--back { left: 50%; top: 50%; transform: translate(-50%, -50%); }
  .brand--back .brand__square { background: var(--accent-sky); }
  .brand--back .brand__name,
  .brand--back .brand__tagline { color: var(--white); }
</style>
</head>
<body>
<main class="canvas">

  <section class="card card--front" aria-label="Business card front">
    <svg class="front-shape" width="540" height="310" viewBox="0 0 540 310" aria-hidden="true">
      <defs>
        <linearGradient id="frontBlue" x1="0" y1="0" x2="1" y2="1">
          <stop offset="0" stop-color="#2d5bb0"/>
          <stop offset="1" stop-color="#1d3a94"/>
        </linearGradient>
      </defs>
      <path d="M0 0 H540 V280 C480 275 420 220 330 195 C220 165 100 180 0 110 Z"
            fill="none" stroke="var(--curve-dark)" stroke-width="10"/>
      <path d="M0 0 H540 V280 C480 275 420 220 330 195 C220 165 100 180 0 110 Z"
            fill="url(#frontBlue)"/>
    </svg>

    <div class="contact">
      <p class="contact__name">DANIEL HART</p>
      <p class="contact__title">Manager</p>
      <p class="contact__address">Unit 4, Marsh Lane<br>Kingsbury, London NW9 0AA</p>
      <ul class="contact__list">
        <li class="contact__row">
          <span class="contact__icon"><svg viewBox="0 0 10 10"><path d="M2 1 L4 3 L3 4 C4 5.5 4.5 6 6 7 L7 6 L9 8 L8 9 C4 9 1 6 1 2 Z" fill="var(--brand-blue)"/></svg></span>
          123 456 7890
        </li>
        <li class="contact__row">
          <span class="contact__icon"><svg viewBox="0 0 10 10"><rect x="3" y="1" width="4" height="8" rx=".8" fill="var(--brand-blue)"/></svg></span>
          123 456 7890
        </li>
        <li class="contact__row">
          <span class="contact__icon"><svg viewBox="0 0 10 10"><rect x="1" y="4" width="8" height="5" fill="var(--brand-blue)"/><rect x="3" y="1" width="4" height="3" fill="var(--brand-blue)"/></svg></span>
          123 456 7890
        </li>
        <li class="contact__row">
          <span class="contact__icon"><svg viewBox="0 0 10 10"><rect x="1" y="2" width="8" height="6" fill="var(--brand-blue)"/><path d="M1 2 L5 5.5 L9 2" fill="none" stroke="#fff" stroke-width=".8"/></svg></span>
          info@oakridgeinteriors.co.uk
        </li>
        <li class="contact__row">
          <span class="contact__icon"><svg viewBox="0 0 10 10"><circle cx="5" cy="5" r="4" fill="none" stroke="var(--brand-blue)" stroke-width="1"/><path d="M1 5 H9 M5 1 C3 3 3 7 5 9 C7 7 7 3 5 1" fill="none" stroke="var(--brand-blue)" stroke-width=".8"/></svg></span>
          www.oakridgeinteriors.co.uk
        </li>
      </ul>
    </div>

    <div class="brand brand--front">
      <span class="brand__square" aria-hidden="true"></span>
      <div>
        <p class="brand__name">Oakridge Interiors</p>
        <p class="brand__tagline">Trade Furniture Solutions</p>
      </div>
    </div>
  </section>

  <section class="card card--back" aria-label="Business card back">
    <div class="brand brand--back">
      <span class="brand__square" aria-hidden="true"></span>
      <div>
        <p class="brand__name">Oakridge Interiors</p>
        <p class="brand__tagline">Trade Furniture Solutions</p>
      </div>
    </div>
  </section>

</main>
</body>
</html>
```